BUSINESS CARD DESIGN

NAME- DALE VORSKIN
PHONE NUMER - 555- 714-9082
EMAIL- OFFICE@TRV-GROUNDMAKRZ.COM
BACK OF CARD- SPEACIALIZES IN LAND CLEARING, FORESTRY MUCLHING AND EXCAVATION

Contact Information for Business Card

NAME- DALE VORSKIN PHONE NUMER - 555- 714-9082 EMAIL- OFFICE@TRV-GROUNDMAKRZ.COM BACK OF CARD- SPEACIALIZES IN LAND CLEARING , MUCLHING AND EXCAVATION

```html
<!DOCTYPE html>
<html lang="en">
<head>
<meta charset="utf-8">
<title>Traverse Groundmakrz LLC — Business Card</title>
<link href="https://fonts.googleapis.com/css2?family=Roboto:wght@300;400;700&display=swap" rel="stylesheet">
<style>
  :root {
    --page: #e3e7e9;
    --card: #202024;
    --accent: #f5ac16;
    --ink-light: #f1f1f1;
  }
  * { margin: 0; padding: 0; box-sizing: border-box; }
  html, body {
    width: 1200px; height: 960px; overflow: hidden;
    background: var(--page);
    font-family: "Roboto", Arial, sans-serif;
  }
  .card {
    position: absolute;
    left: 250px;
    width: 702px; height: 400px;
    background: var(--card);
    border-left: 4px solid var(--accent);
    border-bottom: 3px solid var(--accent);
  }
  .card--front { top: 60px; }
  .card--back { top: 500px; }

  .brand {
    position: absolute; left: 0; right: 0; top: 118px;
    display: flex; flex-direction: column; align-items: center;
    color: var(--accent);
  }
  .brand__mark {
    width: 92px; height: 92px; border-radius: 50%;
    background: var(--accent);
    margin-bottom: 22px;
  }
  .brand__name {
    font-weight: 700; font-size: 24px; letter-spacing: 2px;
  }
  .brand__phone {
    margin-top: 14px;
    font-weight: 400; font-size: 13px; letter-spacing: 9px;
  }
  .tagline {
    position: absolute; left: 0; right: 0; top: 357px;
    text-align: center;
    color: var(--accent);
    font-weight: 400; font-size: 16px; letter-spacing: 0.3px;
  }

  .person {
    position: absolute; left: 20px; top: 176px;
    font-size: 42px; line-height: 1;
    color: var(--accent);
  }
  .person__first { font-weight: 700; }
  .person__last { font-weight: 300; margin-left: 6px; }
  .divider {
    position: absolute; left: 346px; top: 140px;
    width: 1px; height: 120px; background: var(--accent);
  }
  .contacts {
    position: absolute; left: 392px; top: 166px;
    list-style: none;
  }
  .contacts__item {
    display: flex; align-items: center;
    height: 22px;
    color: var(--ink-light);
    font-size: 15px; letter-spacing: 0.6px; font-weight: 400;
  }
  .contacts__icon {
    width: 16px; height: 16px; margin-right: 9px; flex: none;
  }
</style>
</head>
<body>
  <section class="card card--front">
    <div class="brand">
      <div class="brand__mark"></div>
      <div class="brand__name">TRAVERSE GROUNDMAKRZ LLC</div>
      <div class="brand__phone">555-714-9082</div>
    </div>
    <p class="tagline">SPEACIALIZES IN LAND CLEARING , MUCLHING AND EXCAVATION</p>
  </section>

  <section class="card card--back">
    <h1 class="person"><span class="person__first">DALE</span><span class="person__last">VORSKIN</span></h1>
    <div class="divider"></div>
    <ul class="contacts">
      <li class="contacts__item">
        <svg class="contacts__icon" viewBox="0 0 16 16" aria-hidden="true">
          <path d="M3 1.5l2.5 0 1 3.2-1.6 1.2c.8 1.8 2.2 3.2 4 4l1.2-1.6 3.2 1v2.5c0 .8-.7 1.4-1.5 1.3C6.5 12.6 3.4 9.5 2.9 4 2.8 3.1 3 1.5 3 1.5z" fill="var(--accent)"/>
          <path d="M9.5 2.5a4 4 0 0 1 4 4M9.5 4.8a1.8 1.8 0 0 1 1.8 1.8" stroke="var(--accent)" stroke-width="1.2" fill="none"/>
        </svg>
        555- 714-9082
      </li>
      <li class="contacts__item">
        <svg class="contacts__icon" viewBox="0 0 16 16" aria-hidden="true">
          <circle cx="8" cy="8" r="7" fill="var(--accent)"/>
          <path d="M4 4.5c1.5.3 2 1.5 1.4 2.6-.5 1 .7 1.7.4 3M9.5 2.2c-.3 1.3.8 1.8 2 1.6M10 9.5c1.2-.5 2.4.3 2.5 1.5" stroke="var(--card)" stroke-width="1.3" fill="none"/>
        </svg>
        WWW.TRV-GROUNDMAKRZ.COM
      </li>
      <li class="contacts__item">
        <svg class="contacts__icon" viewBox="0 0 16 16" aria-hidden="true">
          <rect x="1" y="6" width="14" height="9" fill="var(--accent)"/>
          <path d="M1 6l7-5 7 5" fill="var(--accent)"/>
          <path d="M1 15l6-4.5h2l6 4.5" stroke="var(--card)" stroke-width="1" fill="none"/>
          <circle cx="8" cy="6.5" r="2" stroke="var(--card)" stroke-width="1" fill="none"/>
        </svg>
        OFFICE@TRV-GROUNDMAKRZ.COM
      </li>
    </ul>
  </section>
</body>
</html>
```